Business Card Design

Business Card for professional consulting firm working with large financial institutions.

Target Market(s)

Executive buyers

Industry/Entity Type

Banking

Contact Information for Business Card

Mild creativity wanted. Not boring, but do elaborate artwork.

Font styles to use
Serif
Sans Serif

Colors

Designer to choose colors to be used in the design.

Requirements
Must have
• Standard business card features - company name, individual name, telephone, website, email, locations.
Nice to have
• Two colors
Should not have
• too many colors, fancy printing, cartoons.

```html
<!DOCTYPE html>
<html lang="en">
<head>
<meta charset="utf-8">
<title>northvane business card</title>
<link rel="stylesheet" href="https://fonts.googleapis.com/css2?family=Roboto:wght@400;500&display=swap">
<style>
  :root {
    --canvas-bg: #e4e2df;
    --panel-grey: #adadad;
    --panel-black: #000000;
    --card-white: #f3f3f3;
    --ink-white: #ffffff;
    --ink-dark: #1a1a1a;
    --mark-grey: #c4c4c4;
  }
  * { margin: 0; padding: 0; box-sizing: border-box; }
  html, body { width: 1200px; height: 960px; overflow: hidden; }
  body {
    position: relative;
    background: var(--canvas-bg);
    font-family: "Roboto", Arial, sans-serif;
  }
  .card {
    position: absolute;
    width: 600px;
    height: 343px;
    box-shadow: 0 2px 5px rgba(0,0,0,0.25);
  }
  .card-front { left: 314px; top: 113px; display: flex; }
  .card-back { left: 311px; top: 472px; background: var(--card-white); }

  .front-brand {
    width: 310px;
    height: 100%;
    background: var(--panel-grey);
    display: flex;
    align-items: center;
    justify-content: center;
  }
  .front-details {
    flex: 1;
    background: var(--panel-black);
    color: var(--ink-white);
    padding: 74px 0 0 61px;
  }
  .wordmark {
    display: flex;
    align-items: center;
    gap: 10px;
    font-family: "Roboto", Arial, sans-serif;
    font-weight: 400;
  }
  .wordmark-dot { width: 12px; height: 12px; border-radius: 50%; }
  .front-brand .wordmark { font-size: 32px; color: var(--ink-white); margin-top: -24px; }
  .front-brand .wordmark-dot { background: var(--ink-white); }
  .card-back .wordmark {
    position: absolute;
    left: 0; right: 0; top: 146px;
    justify-content: center;
    font-size: 36px;
    color: var(--ink-dark);
  }
  .card-back .wordmark-dot { background: var(--mark-grey); }

  .person-name { font-size: 20px; font-weight: 500; letter-spacing: 0.2px; line-height: 24px; }
  .person-title { font-size: 14px; font-weight: 500; line-height: 18px; }
  .address { margin-top: 48px; font-size: 14px; line-height: 17px; }
  .contact-list { list-style: none; margin-top: 12px; font-size: 14px; line-height: 19.5px; }
  .contact-list li { display: flex; align-items: center; gap: 8px; }
  .contact-icon { width: 13px; height: 13px; fill: var(--ink-white); flex: none; }
</style>
</head>
<body>
  <div class="card card-front">
    <div class="front-brand">
      <div class="wordmark"><span class="wordmark-dot"></span>northvane</div>
    </div>
    <div class="front-details">
      <p class="person-name">DANIEL REYES</p>
      <p class="person-title">CEO/FOUNDER</p>
      <p class="address">4120 Alder Court<br>Juneau, Alaska 99801</p>
      <ul class="contact-list">
        <li>
          <svg class="contact-icon" viewBox="0 0 24 24" aria-hidden="true"><path d="M6.6 10.8c1.4 2.8 3.8 5.1 6.6 6.6l2.2-2.2c.3-.3.7-.4 1-.2 1.1.4 2.3.6 3.6.6.6 0 1 .4 1 1V20c0 .6-.4 1-1 1C10.6 21 3 13.4 3 4c0-.6.4-1 1-1h3.5c.6 0 1 .4 1 1 0 1.3.2 2.5.6 3.6.1.3 0 .7-.2 1l-2.3 2.2z"/></svg>
          555 214 7093
        </li>
        <li>
          <svg class="contact-icon" viewBox="0 0 24 24" aria-hidden="true"><path d="M2 5h20v14H2z M4 7v.5l8 5 8-5V7z" fill-rule="evenodd"/></svg>
          hello@northvane.com
        </li>
        <li>
          <svg class="contact-icon" viewBox="0 0 24 24" aria-hidden="true"><circle cx="12" cy="12" r="10"/><path d="M12 2v20M2 12h20" stroke="#000" stroke-width="1.6" fill="none"/></svg>
          www.northvane.com
        </li>
      </ul>
    </div>
  </div>

  <div class="card card-back">
    <div class="wordmark"><span class="wordmark-dot"></span>northvane</div>
  </div>
</body>
</html>
```